BrivoTerna. Lantern of the Steady Harvest. Business card

Professional business card for BrivoTerna (Lantern of the Steady Harvest)
My rationale: Strategy-> Execution-> Results-> Value that lead to the BrivoTerna name: We put the Lantern of the Steady Harvest.
We deliver value to our customers helping them at defining a good strategy (cyan arrow). 90% of well formulated strategies fail due to poor execution so we also consider strategical execution very important (green arrow). Due to the execution we obtain the results (blue arrow). Finally, the results provide feedback to redefine strategy, and the new strategy has to be executed and new results obtained providing new feedback and on and on. It's like a wheel that finally, must create corporate value: value for shareholders, staholders, employees, providers...-

Target Market(s)

CEOs and steering comitees , invewrnent funds

Industry/Entity Type

Business Consultant

Contact Information for Business Card

Teodoro Vinsquel
CEO & Founder
teodoro.vinsquel@brivoterna-example.com
Mobile: +34 655.803.912
www.brivoterna-example.com

Colors

Designer to choose colors to be used in the design.

Requirements
Nice to have
• Nice to hace the words: Strategy, execution, results
• Nice to vave the claim: Lantern of the Steady Harvest
• The three colors should be shown:
• cyan for STRATEGY
• green for EXECUTION
• blue for RESULTS
Should not have
• Complete black background

```html
<!DOCTYPE html>
<html lang="en">
<head>
<meta charset="utf-8">
<title>BrivoTerna business card</title>
<link rel="stylesheet" href="https://fonts.googleapis.com/css2?family=PT+Sans:wght@400;700&family=PT+Sans+Narrow:wght@700&display=swap">
<style>
  :root {
    --backdrop: #e0e0e0;
    --card: #ffffff;
    --navy: #003399;
    --cyan: #00aeef;
    --green: #8dc63f;
    --shadow: rgba(0, 0, 0, 0.28);
  }
  * { box-sizing: border-box; margin: 0; padding: 0; }
  html, body { width: 1130px; height: 1200px; overflow: hidden; }
  body {
    background: var(--backdrop);
    position: relative;
    font-family: "PT Sans", sans-serif;
  }
  .card {
    position: absolute;
    top: 218px;
    width: 436px;
    height: 764px;
    background: var(--card);
    border-radius: 26px;
    overflow: hidden;
    box-shadow: 0 3px 10px var(--shadow);
  }
  .card--front { left: 102px; }
  .card--back { left: 590px; }
  .wordmark {
    position: absolute;
    top: 178px;
    left: 0;
    width: 100%;
    text-align: center;
    font-family: "PT Sans Narrow", sans-serif;
    font-weight: 700;
    font-size: 78px;
    line-height: 1;
    letter-spacing: -1.5px;
    color: var(--navy);
  }
  .person {
    position: absolute;
    top: 338px;
    width: 100%;
    text-align: center;
  }
  .person__name {
    font-weight: 700;
    font-size: 31px;
    color: var(--navy);
    line-height: 1.2;
  }
  .person__role {
    font-size: 24px;
    color: var(--cyan);
    line-height: 1.2;
  }
  .contacts {
    position: absolute;
    top: 460px;
    left: 10px;
    width: 417px;
    list-style: none;
  }
  .contact {
    display: flex;
    height: 32px;
    margin-bottom: 3.5px;
    color: #fff;
    font-size: 18px;
    line-height: 32px;
  }
  .contact__label {
    width: 90px;
    background: var(--cyan);
    border-radius: 6px 0 0 6px;
    text-align: center;
    margin-right: 3px;
  }
  .contact__value {
    flex: 1;
    background: var(--navy);
    border-radius: 0 6px 6px 0;
    padding-left: 11px;
    white-space: nowrap;
  }
  .contact__value--small { font-size: 15.5px; padding-left: 9px; }
  .footer-rule {
    position: absolute;
    left: 0;
    top: 648px;
    width: 100%;
    height: 6px;
    background: var(--green);
  }
  .footer-band {
    position: absolute;
    left: 0;
    top: 660px;
    width: 100%;
    height: 104px;
    background: var(--navy);
  }
  .tagline {
    position: absolute;
    top: 709px;
    width: 100%;
    text-align: center;
    font-weight: 700;
    font-size: 20px;
    letter-spacing: 1.6px;
    color: var(--green);
  }
  .tagline__dot { color: var(--cyan); margin: 0 6px; }
</style>
</head>
<body>

<section class="card card--front" aria-label="Front of card">
  <div class="wordmark">BrivoTerna</div>
  <div class="person">
    <p class="person__name">Teodoro Vinsquel</p>
    <p class="person__role">CEO &amp; Founder</p>
  </div>
  <ul class="contacts">
    <li class="contact"><span class="contact__label">Mobile</span><span class="contact__value">+34 655.803.912</span></li>
    <li class="contact"><span class="contact__label">Email</span><span class="contact__value contact__value--small">teodoro.vinsquel@brivoterna-example.com</span></li>
    <li class="contact"><span class="contact__label">Web</span><span class="contact__value">www.brivoterna-example.com</span></li>
  </ul>
  <div class="footer-rule"></div>
  <div class="footer-band"></div>
  <p class="tagline">RESULTS<span class="tagline__dot">•</span>EXECUTION<span class="tagline__dot">•</span>STRATEGY</p>
</section>

<section class="card card--back" aria-label="Back of card">
  <div class="wordmark">BrivoTerna</div>
  <div class="footer-rule"></div>
  <div class="footer-band"></div>
  <p class="tagline">RESULTS<span class="tagline__dot">•</span>EXECUTION<span class="tagline__dot">•</span>STRATEGY</p>
</section>

</body>
</html>
```